I need a new business card designed, we recently rebranded and I need to get a fresh design to match our new logo, colours and branding.

Details:

Derek Havill | Founder & CEO
Address: 7 Marlowfern Lane, #09-14 Tavenport Crest, Singapore 318547
Tel: +65 93568214
Web: www.frostkarta.com.sg
hello@frostkarta.com.sg

I've attached my old card as well

Industry/Entity Type

Business

Requirements
Must have
• Front and Back
Interesting use of logo
Correct use of colour scheme

```html
<!DOCTYPE html>
<html lang="en">
<head>
<meta charset="utf-8">
<title>Frostkarta Business Card</title>
<link rel="stylesheet" href="https://fonts.googleapis.com/css2?family=Source+Sans+3:wght@400;600;700&display=swap">
<style>
  :root {
    --backdrop: #efece7;
    --card: #ffffff;
    --brand-blue: #38b6ef;
    --box-blue: #0ea6ea;
    --mark-blue: #3fb9f0;
    --faint-blue: #e5f5fc;
    --brand-brown: #7b6b63;
    --label-grey: #5c524b;
    --rule: #8a8580;
  }
  * { margin: 0; padding: 0; box-sizing: border-box; }
  html, body {
    width: 1200px; height: 1000px; overflow: hidden;
    background: var(--backdrop);
    font-family: "Source Sans 3", "Myriad Pro", sans-serif;
  }
  .canvas { position: relative; width: 1200px; height: 1000px; }
  .card {
    position: absolute; background: var(--card);
    border: 1px solid #d9d5cf; overflow: hidden;
  }

  /* Logo side */
  .card-back { left: 354px; top: 139px; width: 729px; height: 416px; }
  .card-back .brand { position: absolute; left: 221px; top: 162px; display: flex; align-items: center; }
  .brand-dot { border-radius: 50%; background: var(--mark-blue); flex: none; }
  .card-back .brand-dot { width: 78px; height: 78px; margin-right: 14px; }
  .brand-name { color: var(--brand-brown); font-weight: 700; line-height: 1; }
  .card-back .brand-name { font-size: 50px; letter-spacing: -0.5px; }
  .brand-tagline { color: var(--brand-blue); font-weight: 700; line-height: 1; letter-spacing: 0.6px; }
  .card-back .brand-tagline { font-size: 12.5px; margin-top: 6px; }

  /* Details side */
  .card-front { left: 87px; top: 508px; width: 715px; height: 417px; }
  .card-front .brand { position: absolute; left: 47px; top: 43px; display: flex; align-items: center; }
  .card-front .brand-dot { width: 41px; height: 41px; margin-right: 8px; }
  .card-front .brand-name { font-size: 25px; }
  .card-front .brand-tagline { font-size: 6.5px; margin-top: 3px; }
  .person { position: absolute; left: 456px; top: 28px; }
  .person-name { color: var(--brand-blue); font-weight: 700; font-size: 35px; letter-spacing: 1.5px; line-height: 1.05; }
  .person-role { color: var(--label-grey); font-size: 25px; line-height: 1; }
  .divider { position: absolute; left: 0; right: 0; top: 116px; height: 1px; background: var(--rule); }
  .watermark-circle {
    position: absolute; left: 186px; top: 92px; width: 290px; height: 290px;
    border-radius: 50%; background: var(--faint-blue);
  }
  .detail { position: absolute; }
  .detail-label { color: var(--label-grey); font-size: 13px; text-transform: uppercase; line-height: 1; }
  .detail-value {
    position: relative; display: inline-block; margin-top: 14px;
    background: var(--box-blue); color: #fff;
    font-size: 16px; line-height: 20px; padding: 8px 8px 9px;
  }
  .detail-value::before {
    content: ""; position: absolute; left: 16px; top: -9px;
    border-left: 9px solid transparent; border-right: 9px solid transparent;
    border-bottom: 10px solid var(--box-blue);
  }
  .detail-web  { left: 46px;  top: 166px; }
  .detail-mail { left: 46px;  top: 264px; }
  .detail-tel  { left: 459px; top: 166px; }
  .detail-addr { left: 459px; top: 264px; }
  .detail-tel .detail-value, .detail-addr .detail-value { min-width: 166px; padding-left: 12px; }
  .detail-addr .detail-value { padding-top: 9px; padding-bottom: 9px; }
</style>
</head>
<body>
<main class="canvas">
  <section class="card card-back" aria-label="Card back">
    <div class="brand">
      <span class="brand-dot"></span>
      <div>
        <div class="brand-name">frostkarta</div>
        <div class="brand-tagline">WEB DESIGN &amp; CONSULTANCY</div>
      </div>
    </div>
  </section>

  <section class="card card-front" aria-label="Card front">
    <div class="watermark-circle" role="img" aria-label="Faint brand circle"></div>
    <div class="brand">
      <span class="brand-dot"></span>
      <div>
        <div class="brand-name">frostkarta</div>
        <div class="brand-tagline">WEB DESIGN &amp; CONSULTANCY</div>
      </div>
    </div>
    <div class="person">
      <div class="person-name">Derek Havill</div>
      <div class="person-role">Founder</div>
    </div>
    <div class="divider"></div>

    <div class="detail detail-web">
      <div class="detail-label">Email</div>
      <div class="detail-value">www.frostkarta.com.sg</div>
    </div>
    <div class="detail detail-mail">
      <div class="detail-label">Web site</div>
      <div class="detail-value">hello@frostkarta.com.sg</div>
    </div>
    <div class="detail detail-tel">
      <div class="detail-label">Contact</div>
      <div class="detail-value">+65&nbsp; 9356 8214</div>
    </div>
    <div class="detail detail-addr">
      <div class="detail-label">Address</div>
      <div class="detail-value">7 Marlowfern Lane,<br>#09-14 Tavenport Crest,<br>Singapore 318547</div>
    </div>
  </section>
</main>
</body>
</html>
```